Venture Capital Investment Firm

We are looking to overhaul our existing website (substantially), with only using the same logos (which we can provide).
We are an investment firm that focuses on making loans to late stage technology companies. Our site should ultimately look like other venture capital firms, and look modern and fresh. We have an existing website www.norvellhub.com which this will be replacing, although we will be using a lot of the existing written content, and potentially the numbers of pages we will need, we are not wed to anything else. Please feel free to shoot any questions at any time and thank you in advance for your help!
Websites we like as examples:
https://www.tesmarkfund.com/
https://www.brindlewoodpartners.com/
Target Market(s)
Potential investors who will invest in our firm, as well as potentially companies that are looking to borrow money from us.
Coding
Coded - Design and coding required
Number of Pages Required
5+ page
Colors
Designer to choose colors to be used in the design.
Look and feel

```html
<!DOCTYPE html>
<html lang="en">
<head>
<meta charset="utf-8">
<title>Norvell Partners — Our Values</title>
<link rel="stylesheet" href="https://fonts.googleapis.com/css2?family=Cinzel:wght@600;700&family=Montserrat:wght@400;500&display=swap">
<style>
:root{
  --navy:#0c0c4e;
  --ink:#4a4a55;
  --muted:#7a7a82;
  --panel:#f3f3f4;
  --tile:#f1f1f3;
  --tile-line:#dfdfe4;
  --footer:#0505a0;
  --footer-field:#1a1aad;
  --white:#ffffff;
}
*{box-sizing:border-box;margin:0;padding:0}
html,body{width:1200px;height:3284px;overflow:hidden;background:var(--white)}
body{position:relative;font-family:"Montserrat",sans-serif;color:var(--ink)}
.abs{position:absolute}
.serif{font-family:"Cinzel",serif;font-weight:700;color:var(--navy)}
.brand{left:79px;top:118px;display:flex;align-items:center;gap:22px;font-size:104px;line-height:1;letter-spacing:2px}
.brand-dot{width:26px;height:26px;border-radius:50%;background:var(--navy)}
.nav{left:769px;top:65px;width:353px;height:571px;display:grid;grid-template-columns:1fr 1fr;grid-template-rows:repeat(3,1fr);border:1px solid var(--tile-line);background:var(--tile)}
.nav-tile{border-right:1px solid var(--tile-line);border-bottom:1px solid var(--tile-line);display:flex;flex-direction:column;align-items:center;justify-content:center;gap:14px;text-align:center;font-size:15px;line-height:29px;color:#33335a}
.nav-tile:nth-child(2n){border-right:none}
.nav-tile:nth-child(n+5){border-bottom:none}
.nav-tile svg{width:44px;height:52px;stroke:var(--navy);fill:none;stroke-width:1.6}
.page-icon{left:79px;top:373px;width:38px;height:52px;stroke:var(--navy);fill:none;stroke-width:2}
.page-title{left:79px;top:436px;font-size:48px;letter-spacing:1px}
.page-sub{left:79px;top:506px;font-size:22px;line-height:33px;color:#2a2a44;letter-spacing:.5px}
.hero-visual{left:77px;top:718px;width:544px;height:386px;background:linear-gradient(135deg,#0a0f40 0%,#1d2a78 45%,#6f92d8 70%,#1a2466 100%)}
.body-text{font-size:14px;line-height:27px;color:var(--ink)}
.intro{left:669px;top:734px;width:460px}
.band{left:0;width:1200px;background:var(--panel)}
.sec-title{font-size:41px;line-height:43px;letter-spacing:.5px}
.sec-kicker{font-size:15px;color:#2a2a44;letter-spacing:.3px}
.stat{width:230px;text-align:center}
.stat-head{font-family:"Cinzel",serif;font-weight:700;color:var(--navy);font-size:25px;line-height:47px}
.stat-sub{font-size:14px;color:var(--muted);margin-top:4px}
.footer{left:0;top:2878px;width:1200px;height:345px;background:var(--footer);color:var(--white)}
.f-brand{left:98px;top:112px;display:flex;align-items:center;gap:14px;font-family:"Cinzel",serif;font-weight:600;font-size:34px}
.f-brand-dot{width:14px;height:14px;border-radius:50%;background:var(--white)}
.legal{left:175px;top:190px;font-size:15px;color:#e6e6ff;text-decoration:underline}
.f-head{font-family:"Cinzel",serif;font-weight:700;font-size:19px;letter-spacing:.5px}
.f-text{font-size:14px;line-height:27px;color:#dcdcff}
.f-icon{fill:var(--white)}
.field{left:790px;width:323px;height:46px;background:var(--footer-field);font-size:14px;color:#dcdcff;padding:15px 16px}
.subscribe{left:790px;top:250px;width:161px;height:52px;border-radius:26px;background:var(--white);color:var(--navy);font-family:"Cinzel",serif;font-weight:700;font-size:17px;letter-spacing:1px;display:flex;align-items:center;justify-content:center}
.copyright{left:0;top:3223px;width:1200px;height:61px;background:var(--panel);display:flex;align-items:center;justify-content:center;font-size:14px;color:#3a3a55}
</style>
</head>
<body>

<header>
  <div class="abs brand serif"><span class="brand-dot"></span>NORVELL</div>

  <nav class="abs nav">
    <div class="nav-tile">
      <svg viewBox="0 0 44 52"><path d="M22 4a14 14 0 0 0-8 25v7h16v-7a14 14 0 0 0-8-25z"/><path d="M15 40h14M16 44h12M19 48h6"/></svg>
      <span>WE STARTED<br>WITH A BIG IDEA</span>
    </div>
    <div class="nav-tile">
      <svg viewBox="0 0 44 52"><circle cx="16" cy="30" r="9"/><circle cx="16" cy="30" r="4"/><circle cx="31" cy="18" r="7"/><circle cx="31" cy="18" r="3"/><circle cx="33" cy="34" r="5"/></svg>
      <span>WHAT WE LOOK<br>FOR</span>
    </div>
    <div class="nav-tile">
      <svg viewBox="0 0 44 52"><circle cx="22" cy="18" r="7"/><circle cx="11" cy="22" r="5"/><circle cx="33" cy="22" r="5"/><path d="M8 42c0-8 6-14 14-14s14 6 14 14zM2 38c0-6 4-9 9-9M42 38c0-6-4-9-9-9"/></svg>
      <span>OUR TEAM</span>
    </div>
    <div class="nav-tile">
      <svg viewBox="0 0 44 52"><circle cx="22" cy="18" r="14"/><circle cx="22" cy="18" r="9"/><path d="M18 18l3 3 5-6M13 30l-4 16 6-4 4 6 3-12M31 30l4 16-6-4-4 6-3-12"/></svg>
      <span>OUR VALUES</span>
    </div>
    <div class="nav-tile">
      <svg viewBox="0 0 44 52"><circle cx="24" cy="14" r="9"/><path d="M24 8v12M21 11h5M21 17h5M4 36l8-4h12l-8 2M12 32l10 10 18-10M24 24v8"/></svg>
      <span>OUR INVESTMENTS</span>
    </div>
    <div class="nav-tile">
      <svg viewBox="0 0 44 52"><rect x="4" y="10" width="36" height="32"/><path d="M8 6h32M12 18h22M12 24h22M12 30h22M12 36h22"/></svg>
      <span>NEWS</span>
    </div>
  </nav>

  <svg class="abs page-icon" viewBox="0 0 38 52"><circle cx="19" cy="17" r="14"/><circle cx="19" cy="17" r="9"/><path d="M14 17l4 4 6-7M10 28l-4 20 7-4 5 6 1-14M28 28l4 20-7-4-5 6"/></svg>
  <h1 class="abs page-title serif">OUR VALUES</h1>
  <p class="abs page-sub">IDENTIFY SITUATIONS WHERE OUR<br>STRUCTURED FINANCING ALTERNATIVES</p>
</header>

<section>
  <div class="abs hero-visual" role="img" aria-label="Blue-toned view looking up at glass office towers"></div>
  <p class="abs body-text intro">We seek to fill a void in the capital markets where too often complexity and perceived risk penalize innovative companies with proven products.&nbsp; We apply our team's deep domain knowledge to identify situations where our structured financing alternatives can deliver a lower cost of capital than traditional venture capital or growth equity and allow our transaction partners to avoid significant dilution at sub-optimal valuations.&nbsp; We also target situations where venture loans and commercial banks are not attractive or viable options given the limited amount of debt capital offered, near-term principal amortization, requirements for substantial liquidity after investment, and the regimented criteria these lenders often focus on prior to extending credit.</p>
</section>

<section class="abs band" style="top:1205px;height:677px">
  <h2 class="abs sec-title serif" style="left:82px;top:98px">STRUCTURED CREDIT</h2>
  <p class="abs sec-kicker" style="left:84px;top:155px">KEY BENEFITS FOR STRUCTURED CREDIT</p>
  <p class="abs body-text" style="left:620px;top:98px;width:500px">We offer revenue-generating companies in the life science and technology industries bespoke loans which offer multiple benefits:</p>

  <div class="abs stat" style="left:79px;top:268px"><div class="stat-head">$10-250M+</div><div class="stat-sub">Sizeable</div></div>
  <div class="abs stat" style="left:350px;top:268px"><div class="stat-head">LONG-TERM<br>MATURITY DATES</div><div class="stat-sub">Flexible</div></div>
  <div class="abs stat" style="left:621px;top:268px"><div class="stat-head">MINIMALLY<br>DILUTIVE</div><div class="stat-sub">Efficient</div></div>

  <p class="abs body-text" style="left:79px;top:422px;width:1050px">Structured credit offers an attractive financing alternative that allows companies to reach value inflection prior to a sale, IPO, or equity financing in order to maximize investor return. Fundamentally different than venture debt, our facilities are long-term, typically without amortization of principal prior to maturity.</p>
  <p class="abs body-text" style="left:79px;top:530px;width:1050px">Our financings are designed to allow our transaction partners to realize the value of businesses they have built. We recognize that proprietary assets generating high margins are highly sought after by strategic buyers and represent collateral that can be unlocked in ways that are under-appreciated by traditional lenders.</p>
</section>

<section class="abs" style="left:0;top:1882px;width:1200px;height:500px">
  <h2 class="abs sec-title serif" style="left:79px;top:78px">MILESTONES &amp;<br>ROYALTIES</h2>
  <p class="abs sec-kicker" style="left:82px;top:172px">KEY BENEFITS FOR MILESTONES &amp; ROYALTIES</p>
  <p class="abs body-text" style="left:618px;top:76px;width:505px">We offer owners of milestones &amp; royalty rights the ability to monetize or securitize future cash flows ranging from $10-250M.</p>
  <p class="abs body-text" style="left:79px;top:246px;width:1050px">Norvell Partners has the ability to structure its transactions in a variety of ways depending on the specific attributes of milestone &amp; royalty payments and the funding requirements and circumstances of each royalty recipient&nbsp; - whether an inventor, university, research institute, hospital, or company.</p>
  <p class="abs body-text" style="left:79px;top:354px;width:1050px">Quantifying and appropriately valuing payment streams created through the licensing of IP is a core strength of our team and we work closely with royalty recipients to understand their entitlements and create an optimal financial structure.</p>
</section>

<section class="abs band" style="top:2382px;height:496px">
  <h2 class="abs sec-title serif" style="left:82px;top:100px">LEGACY ASSETS</h2>
  <p class="abs sec-kicker" style="left:79px;top:160px">KEY BENEFITS FOR LEGACY ASSETS</p>
  <p class="abs body-text" style="left:620px;top:98px;width:505px">We offer companies with mature, "non-core" assets upfront capital in exchange for products that are no longer strategic to their businesses.</p>
  <p class="abs body-text" style="left:79px;top:239px;width:1050px">The partners of Norvell Partners have successfully acquired over $300M of these "legacy assets", which frequently are off-patent branded generics, from large pharmaceutical companies.&nbsp; We have extensive experience partnering with entrepreneurial teams - typically industry executives with a deep knowledge of specific products - to acquire and manage these brands in ways that maintain and strengthen their value over time.&nbsp; Our focus is on products in stable markets that offer highly predictable cash flows.</p>
  <p class="abs body-text" style="left:79px;top:374px;width:1050px">Our transactions enable our counterparties to invest in higher return activities such as acquiring new technologies, financing development projects, and meeting additional working capital needs.</p>
</section>

<footer class="abs footer">
  <div class="abs f-brand"><span class="f-brand-dot"></span>NORVELL</div>
  <span class="abs legal">Legal Disclaimer</span>

  <h3 class="abs f-head" style="left:435px;top:32px">CONTACT US</h3>
  <svg class="abs f-icon" style="left:433px;top:80px" width="18" height="28" viewBox="0 0 18 28"><path d="M9 0a9 9 0 0 0-9 9c0 7 9 19 9 19s9-12 9-19a9 9 0 0 0-9-9zm0 13a4 4 0 1 1 0-8 4 4 0 0 1 0 8z"/></svg>
  <p class="abs f-text" style="left:483px;top:72px">SAN FRANCISCO<br>480 Harlow Street #210<br>San Francisco, CA&nbsp; 94103</p>
  <svg class="abs f-icon" style="left:433px;top:184px" width="22" height="17" viewBox="0 0 22 17"><path d="M0 0h22v3L11 10 0 3zM0 5l11 7 11-7v12H0z"/></svg>
  <p class="abs f-text" style="left:483px;top:175px">GENERAL INQUIRIES : :<br>inquiries@norvellhub.com</p>
  <svg class="abs f-icon" style="left:433px;top:254px" width="22" height="17" viewBox="0 0 22 17"><path d="M0 0h22v3L11 10 0 3zM0 5l11 7 11-7v12H0z"/></svg>
  <p class="abs f-text" style="left:483px;top:245px">MEDIA INQUIRIES :<br>media@norvellhub.com</p>

  <h3 class="abs f-head" style="left:792px;top:32px">NEWSLETTER</h3>
  <p class="abs f-text" style="left:792px;top:72px;width:330px">Would you like to receive our exclusive news and update for signup our newsletter !</p>
  <div class="abs field" style="top:140px">Enter Name *</div>
  <div class="abs field" style="top:195px">Enter Email *</div>
  <div class="abs subscribe">SUBSCRIBE</div>
</footer>

<div class="abs copyright">©2019 Norvell Partners LLC.&nbsp; All Rights Reserved.</div>

</body>
</html>
```